Letterhead, stationery and email signature for construction business

I need the letterhead, stationery and email signature designs for a construction business. I want them to have a corporate feel to them.

I've attached the logo for reference.

```html
<!DOCTYPE html>
<html lang="en">
<head>
<meta charset="utf-8">
<title>Harrow Build – Business Cards</title>
<link rel="stylesheet" href="https://fonts.googleapis.com/css2?family=Roboto:wght@400;700;900&display=swap">
<style>
  :root {
    --backdrop: #d1d4d5;
    --card: #f6f6f5;
    --brand-blue: #1c2f8c;
    --ink: #2b2b2e;
    --muted: #4a4a4f;
    --rule: #6b6b70;
  }
  * { box-sizing: border-box; margin: 0; padding: 0; }
  html, body {
    width: 1200px; height: 991px; overflow: hidden;
    background: var(--backdrop);
    font-family: "Roboto", sans-serif;
  }
  .stage { position: relative; width: 1200px; height: 991px; }
  .card {
    position: absolute; top: 340px;
    width: 540px; height: 310px;
    background: var(--card);
    border-bottom: 4px solid var(--brand-blue);
    box-shadow: 0 10px 24px rgba(0,0,0,0.12);
  }
  .card--back { left: 40px; }
  .card--front { left: 620px; display: flex; align-items: center; justify-content: center; }

  .brand { display: flex; align-items: center; gap: 12px; white-space: nowrap; }
  .brand__mark { width: 40px; height: 40px; background: var(--brand-blue); flex: none; }
  .brand__name {
    font-weight: 900; color: var(--brand-blue);
    font-size: 34px; letter-spacing: 1px; text-transform: uppercase; line-height: 1;
  }
  .card--front .brand__mark { width: 56px; height: 56px; }
  .card--front .brand__name { font-size: 46px; }

  .card--back .brand { position: absolute; left: 30px; top: 88px; gap: 10px; }
  .card--back .brand__mark { width: 30px; height: 30px; }
  .card--back .brand__name { font-size: 23px; letter-spacing: 0.5px; }

  .divider {
    position: absolute; left: 300px; top: 56px; width: 1px; height: 200px;
    background: var(--rule);
  }
  .contact { position: absolute; left: 320px; top: 56px; right: 16px; }
  .contact__name {
    font-weight: 700; color: var(--brand-blue); font-size: 19px;
    text-transform: uppercase; letter-spacing: 0.3px;
  }
  .contact__role { font-weight: 700; color: var(--ink); font-size: 14px; margin-top: 2px; }
  .contact__list { list-style: none; margin-top: 18px; }
  .contact__list li {
    display: flex; align-items: center; gap: 7px;
    font-size: 13.5px; color: var(--muted); line-height: 22px;
  }
  .contact__list svg { width: 13px; height: 13px; flex: none; }
  .contact__address { font-size: 13px; color: var(--muted); line-height: 18px; margin-top: 8px; }
</style>
</head>
<body>
<main class="stage">
  <section class="card card--back" aria-label="Business card, contact side">
    <div class="brand">
      <span class="brand__mark"></span>
      <span class="brand__name">Harrow Build</span>
    </div>
    <div class="divider"></div>
    <div class="contact">
      <p class="contact__name">Daniel Moore</p>
      <p class="contact__role">President</p>
      <ul class="contact__list">
        <li>
          <svg viewBox="0 0 24 24" aria-hidden="true"><path fill="#1c2f8c" d="M6.6 10.8a15 15 0 0 0 6.6 6.6l2.2-2.2c.3-.3.7-.4 1-.2 1.1.4 2.3.6 3.6.6.6 0 1 .4 1 1V20c0 .6-.4 1-1 1A17 17 0 0 1 3 4c0-.6.4-1 1-1h3.5c.6 0 1 .4 1 1 0 1.3.2 2.5.6 3.6.1.3 0 .7-.2 1z"/></svg>
          (555) 318-4420
        </li>
        <li>
          <svg viewBox="0 0 24 24" aria-hidden="true"><rect x="2" y="5" width="20" height="14" fill="none" stroke="#1c2f8c" stroke-width="2"/><path d="M2 5l10 8 10-8" fill="none" stroke="#1c2f8c" stroke-width="2"/></svg>
          info@harrowbuild.com
        </li>
        <li>
          <svg viewBox="0 0 24 24" aria-hidden="true"><g fill="none" stroke="#1c2f8c" stroke-width="1.8"><circle cx="12" cy="12" r="10"/><ellipse cx="12" cy="12" rx="4" ry="10"/><path d="M2 12h20M4 7h16M4 17h16"/></g></svg>
          www.harrowbuild.com
        </li>
      </ul>
      <p class="contact__address">Harrow Build, Ltd.<br>Kestrel House, 14 Marlow Road<br>London SE4 1QT</p>
    </div>
  </section>

  <section class="card card--front" aria-label="Business card, brand side">
    <div class="brand">
      <span class="brand__mark"></span>
      <span class="brand__name">Harrow Build</span>
    </div>
  </section>
</main>
</body>
</html>
```